accomplished personal trainer, former elite gymnast from Russia, highly professional and experienced

Established Fitness trainer in California requires a new web site to attract personal clients and build her group exercise classes.

Here is an example of another fitness trainer's site that I really liked the technology:
http://www.tedvorlam.com

Below I have inserted my current web site: www.quelbornfitnesslodi.com
You can use this web site for the principal content, such as my background and qualifications.

Target Market(s)

Anyone who wants to improve their fitness levels and wellness in general. Anyone who needs directions and instruction on how to exercise. I can train anyone from elite athlete to a disabled person.

Industry/Entity Type

Fitness

Coding

Coded - Design and coding required

Number of Pages Required

5+ page

Font styles to use
Sans Serif

Requirements
Must have
• Easy to navigate main info about me, location, services, contact, benefits of using my services.
• Would be great to create unique representation of me as a trainer and a person, using new technologies and new ideas. Make it different from the other websites. Having its own character. Not too complicated and heavy with information, but an eye catching, useful and fun to navigate.
Nice to have
• new technology, easy access to information, the idea of enjoyment of life, lightness about achieving any goal, spiritual wisdom, unique design. I am planning to insert educational videos, advise, maybe jokes. Sign in, shopping cart, logo, should be easy for me to make changes in content.
Should not have
• cliché, outdated technology, too complicated,

```html
<!DOCTYPE html>
<html lang="en">
<head>
<meta charset="utf-8">
<title>Quelborn Fitness Lodi</title>
<link href="https://fonts.googleapis.com/css2?family=Montserrat:wght@400;600;700&family=Arimo:wght@400;700&display=swap" rel="stylesheet">
<style>
:root{
  --green:#1f9a3c;
  --green-dark:#17803a;
  --navy:#1b4f8a;
  --blue:#1d62aa;
  --text:#555;
  --muted:#777;
  --light:#f4f5f6;
  --line:#e3e3e3;
  --white:#fff;
}
*{margin:0;padding:0;box-sizing:border-box}
html,body{width:1200px;height:4027px;overflow:hidden}
body{position:relative;background:var(--white);font-family:"Arimo",Arial,sans-serif;color:var(--text)}
.abs{position:absolute}
.header{left:0;top:0;width:1200px;height:92px;background:var(--white)}
.brand{left:84px;top:34px;font-family:"Montserrat",sans-serif;font-weight:700;font-size:22px;color:var(--green);letter-spacing:.3px;white-space:nowrap}
.nav{right:84px;top:41px;display:flex;gap:28px;font-family:"Montserrat",sans-serif;font-weight:600;font-size:12px;color:#333;text-transform:uppercase;white-space:nowrap}
.nav .active{color:var(--green)}
.photo{display:block}
.hero{left:0;top:92px;width:1200px;height:565px;background:linear-gradient(180deg,#5f8a4a 0%,#8eb062 45%,#6fa94a 75%,#4d8d34 100%)}
.hero-title{left:84px;top:505px;background:rgba(20,60,20,.55);color:#fff;font-family:"Montserrat",sans-serif;font-weight:700;font-size:27px;padding:7px 18px;letter-spacing:.5px}
.hero-sub{left:84px;top:556px;background:var(--green);color:#fff;font-family:"Montserrat",sans-serif;font-weight:700;font-size:14px;padding:11px 18px}
.dots{left:1080px;top:636px;display:flex;gap:7px}
.dots span{width:7px;height:7px;border-radius:50%;background:#fff;opacity:.6}
.dots span.on{opacity:1}
.video{left:84px;top:720px;width:588px;height:346px;background:linear-gradient(160deg,#8fa37a,#c7b8a8 50%,#6f8a5c)}
.play{left:350px;top:870px}
.feature{left:712px;top:738px;width:384px}
h2.blue{font-family:"Montserrat",sans-serif;font-weight:700;font-size:19px;color:var(--blue);margin-bottom:20px}
p.body{font-size:12.5px;line-height:24px;color:var(--text);margin-bottom:16px}
.btn-navy{display:inline-block;background:var(--navy);color:#fff;font-family:"Montserrat",sans-serif;font-weight:700;font-size:13px;text-align:center}
.band{left:0;top:1128px;width:1200px;height:445px;background:linear-gradient(180deg,#6f8e55,#93ad6e 50%,#5a7f3e)}
.advise{left:0;top:1573px;width:1200px;height:274px;background:var(--light);text-align:center}
h2.green{font-family:"Montserrat",sans-serif;font-weight:700;color:var(--green)}
.advise h2{font-size:28px;padding-top:38px}
.advise p{width:720px;margin:22px auto 0;font-size:12.5px;line-height:24px}
.btn-outline{display:inline-block;border:2px solid var(--green);color:var(--green);font-family:"Montserrat",sans-serif;font-weight:600;font-size:13px;text-align:center;background:#fff}
.advise .btn-outline{margin-top:28px;width:242px;height:43px;line-height:39px}
.row h3{font-family:"Montserrat",sans-serif;font-weight:700;font-size:21px;color:var(--green);margin-bottom:22px}
.row p{font-size:12.5px;line-height:27px}
.row .btn-outline{margin-top:24px;width:121px;height:41px;line-height:37px}
.circle{border-radius:50%}
.divider{left:84px;width:1032px;height:1px;background:var(--line)}
.photo2{left:0;top:2819px;width:1200px;height:424px;background:linear-gradient(180deg,#3f5f2e,#7aa052 55%,#5c8f3a)}
.testi{left:0;top:3243px;width:1200px;text-align:center}
.testi h2{font-size:29px;padding-top:50px}
.quote{margin:22px auto 0;width:68px;height:68px;border:2px solid var(--green);border-radius:50%}
.testi p{width:680px;margin:30px auto 0;font-size:12.5px;line-height:30px}
.stars{margin-top:12px}
.testi .name{margin-top:6px;font-size:14px;color:var(--green);font-weight:700}
.newsletter{left:0;top:3611px;width:1200px;height:336px;background:var(--light)}
.newsletter h2{text-align:center;font-size:22px;padding-top:48px}
.newsletter .lead{text-align:center;font-size:14px;color:var(--muted);margin-top:14px}
.field{background:#fff;border:1px solid #d9d9d9;height:41px;font-size:12px;color:#999;padding:13px 16px}
.signup{left:518px;top:3864px;width:164px;height:43px;line-height:43px}
.footer{left:0;top:3947px;width:1200px;height:80px;background:var(--green-dark)}
.copy{left:84px;top:32px;font-size:12px;color:#fff}
.social{left:906px;top:21px;display:flex;gap:8px}
.social span{width:36px;height:36px;border-radius:50%;border:2px solid #fff}
</style>
</head>
<body>

<header class="abs header">
  <div class="abs brand">QUELBORN FITNESS LODI</div>
  <nav class="abs nav">
    <span class="active">Home</span><span>Group Classes</span><span>Personal Training</span><span>About Quelborn</span><span>Contact</span><span>Blog</span>
  </nav>
</header>

<section class="abs hero photo" role="img" aria-label="Group of people doing squats outdoors on a park lawn"></section>
<div class="abs hero-title">FITNESS OUTDOORS</div>
<div class="abs hero-sub">QUELBORN GROUP EXERCISE CLASSES ARE DESIGNED FOR PEOPLE</div>
<div class="abs dots"><span></span><span class="on"></span><span></span></div>

<div class="abs video photo" role="img" aria-label="Video still of a trainer stretching on a mat outdoors"></div>
<svg class="abs play" width="60" height="42" viewBox="0 0 60 42"><rect width="60" height="42" rx="10" fill="#e02b20"/><path d="M24 12 L40 21 L24 30Z" fill="#fff"/></svg>

<section class="abs feature">
  <h2 class="blue">FEATURE EDUCATIONAL VIDEOS</h2>
  <p class="body">Quelborn Group Exercise classes are designed for people of all fitness levels. Quelborn's group classes take a holistic approach and make sure you work out in a balanced way that feeds your body and spirit. Classes are taught with a variety of approaches including pilates, yoga, strap work, dance, and much more to keep things fresh and challenging.</p>
  <p class="body">Quelborn's group classes take a holistic approach and make sure you work out in a balanced way that feeds your body and spirit. Classes are taught much more to keep things fresh and challenging.</p>
  <span class="btn-navy" style="width:153px;height:43px;line-height:43px;margin-top:6px">WATCH VIDEO</span>
</section>

<div class="abs band photo" role="img" aria-label="Group of smiling people stretching arms overhead in a park"></div>

<section class="abs advise">
  <h2 class="green">ADVISE / TIPS TO MEMBERS</h2>
  <p>Quelborn Group Exercise classes are designed for people of all fitness levels. Quelborn's group classes take a holistic approach and make sure you work out in a balanced way that feeds your body and spirit. Classes are taught with a variety of approaches including pilates, yoga, strap work, dance, and much more to keep things fresh and challenging.</p>
  <span class="btn-outline">CLICK HERE FOR MORE INFO</span>
</section>

<section class="abs row" style="left:148px;top:1915px;width:596px">
  <h3>GROUP CLASSES/ BOOT CAMPS</h3>
  <p>Quelborn Group Exercise classes are designed for people of all fitness levels. Quelborn's group classes take a holistic approach and make sure you work out in a balanced way that feeds your body and spirit. Classes are taught with a variety of approaches including pilates, yoga, strap work, dance, and much more to keep things fresh and pproach and make sure you work out in a balanced way that feeds your body and spirit challenging.</p>
  <span class="btn-outline">READ MORE</span>
</section>
<div class="abs circle photo" style="left:819px;top:1895px;width:241px;height:241px;background:linear-gradient(160deg,#7a9a55,#b58aa0 55%,#6d8a45)" role="img" aria-label="Trainer in pink top stretching on the grass"></div>

<div class="abs divider" style="top:2180px"></div>

<div class="abs circle photo" style="left:148px;top:2202px;width:241px;height:241px;background:linear-gradient(160deg,#6e8f4c,#8fb0a8 55%,#4f7335)" role="img" aria-label="Trainer coaching a client on suspension straps"></div>
<section class="abs row" style="left:465px;top:2224px;width:600px">
  <h3>PERSONAL TRAINING</h3>
  <p>Quelborn Group Exercise classes are designed for people of all fitness levels. Quelborn's group classes take a holistic approach and make sure you work out in a balanced way that feeds your body and spirit. Classes are taught with a variety of approaches including pilates, yoga, strap work, dance, and much more to keep things fresh and pproach and make sure you work out in a balanced way that feeds your body and spirit challenging.</p>
  <span class="btn-outline">READ MORE</span>
</section>

<div class="abs divider" style="top:2486px"></div>

<section class="abs row" style="left:148px;top:2533px;width:596px">
  <h3>ABOUT QUELBORN FITNESS</h3>
  <p>Quelborn Group Exercise classes are designed for people of all fitness levels. Quelborn's group classes take a holistic approach and make sure you work out in a balanced way that feeds your body and spirit. Classes are taught with a variety of approaches including pilates, yoga, strap work, dance, and much more to keep things fresh and pproach and make sure you work out in a balanced way that feeds your body and spirit challenging.</p>
  <span class="btn-outline">READ MORE</span>
</section>
<div class="abs circle photo" style="left:819px;top:2510px;width:241px;height:241px;background:linear-gradient(160deg,#6a8a45,#4fb5b0 55%,#5d7d3a)" role="img" aria-label="Portrait of the trainer in a teal top outdoors"></div>

<div class="abs photo2 photo" role="img" aria-label="Trainer in pink top stretching with arms raised on a lawn"></div>

<section class="abs testi">
  <h2 class="green">OUR TESTIMONIALS</h2>
  <div class="quote"><svg width="64" height="64" viewBox="0 0 64 64"><path d="M22 36c0-6 3-10 8-12l1 3c-3 1-4 3-4 5h3v8h-8zM34 36c0-6 3-10 8-12l1 3c-3 1-4 3-4 5h3v8h-8z" fill="#1f9a3c"/></svg></div>
  <p>I have known Marina for many years as a fitness trainer and workout class instructor. She is truly one of the very best in the business. Marina is extremely knowledgeable about human physiology and teaching. Her personality is professional, informative, and caring. She would always put "her all" into each of her lessons.</p>
  <div class="stars"><svg width="100" height="18" viewBox="0 0 100 18"><g fill="none" stroke="#e6a817" stroke-width="1.2"><path id="s" d="M9 1l2.4 5.2 5.6.6-4.2 3.8 1.2 5.6L9 13.3 4 16.2l1.2-5.6L1 6.8l5.6-.6z"/><use href="#s" x="20"/><use href="#s" x="40"/><use href="#s" x="60"/><use href="#s" x="80"/></g></svg></div>
  <div class="name">Name : Helen Marsh</div>
</section>

<section class="abs newsletter">
  <h2 class="green">NEWSLETTER SUBSCRIBE</h2>
  <div class="lead">Sign up with your email address to receive the latest news and updates.</div>
</section>
<div class="abs field" style="left:220px;top:3754px;width:245px">Name :</div>
<div class="abs field" style="left:481px;top:3754px;width:244px">Email :</div>
<div class="abs field" style="left:736px;top:3754px;width:244px">Phone :</div>
<div class="abs field" style="left:220px;top:3807px;width:760px;height:43px">Message :</div>
<span class="abs btn-navy signup">SIGNUP</span>

<footer class="abs footer">
  <div class="abs copy">© Copyrights 2016 QUELBORN FITNESS LODI All Rights Reserved.</div>
  <div class="abs social"><span></span><span></span><span></span><span></span><span></span></div>
</footer>

</body>
</html>
```